high end kitchens , needing new logo and business card design .

im looking a very simple looking design but classy that will stand out , i would like the design to be in the colours black , silver , gold and grey , although all colours dont need to be used in design , back of card to have name on it derek fawcett , address and phone number and website address , maybe fb logo . adrress is 42 mill row , ashbrook , bt19 4qa , 07912488265 , front of the card im open to design , back of card very simple i will want it matt black with silver writing , writing doesnt need to be that big

Target Market(s)

people with kitchen projects .

Industry/Entity Type

Interior Design

Contact Information for Business Card

front of business card th on it with maybe tallow hearths under it wrote smaller , maybe the card to be mate black with the writing in a gloss black or silver

Logo Text

th . tallow hearths

Font styles to use
Sans Serif
Script

Colors
1b1b1b
919191
f6f6f6
848484
ffc214
ec1f27

Requirements
Must have
• clean and simple , not too fussy ,
Nice to have
• n/a
Should not have
• n/a

```html
<!DOCTYPE html>
<html lang="en">
<head>
<meta charset="utf-8">
<title>Tallow Hearths — Business Card</title>
<link rel="stylesheet" href="https://fonts.googleapis.com/css2?family=Libre+Caslon+Text:wght@400;700&family=Didact+Gothic&display=swap">
<style>
  :root {
    --backdrop: #bfe3d8;
    --card-black: #0b0b0b;
    --card-white: #ffffff;
    --ink: #111111;
    --silver: #e6e6e6;
    --rule: #1b1b1b;
  }
  * { margin: 0; padding: 0; box-sizing: border-box; }
  html, body {
    width: 1200px;
    height: 856px;
    overflow: hidden;
  }
  body {
    background: var(--backdrop);
    display: flex;
    align-items: center;
    justify-content: center;
    gap: 56px;
  }
  .card {
    width: 504px;
    height: 288px;
    border-radius: 30px;
    position: relative;
    box-shadow: 0 8px 18px rgba(0, 0, 0, 0.12);
  }

  /* Brand side */
  .card--brand {
    background: var(--card-black);
    color: var(--silver);
    display: flex;
    flex-direction: column;
    align-items: center;
    justify-content: center;
    gap: 16px;
  }
  .brand-mark {
    width: 92px;
    height: 92px;
  }
  .brand-name {
    font-family: "Libre Caslon Text", serif;
    font-weight: 400;
    font-size: 11px;
    letter-spacing: 0.42em;
    text-transform: uppercase;
    color: var(--silver);
    white-space: nowrap;
  }

  /* Contact side */
  .card--contact {
    background: var(--card-white);
    color: var(--ink);
  }
  .contact-name {
    position: absolute;
    left: 52px;
    top: 110px;
    font-family: "Libre Caslon Text", serif;
    font-weight: 700;
    font-size: 18px;
    line-height: 26px;
    letter-spacing: 0.14em;
    text-transform: uppercase;
    white-space: nowrap;
  }
  .contact-divider {
    position: absolute;
    left: 282px;
    top: 92px;
    width: 1px;
    height: 62px;
    background: var(--rule);
  }
  .contact-details {
    position: absolute;
    left: 298px;
    top: 93px;
    list-style: none;
    font-family: "Didact Gothic", sans-serif;
    font-size: 13px;
    line-height: 20px;
    letter-spacing: 0.04em;
    white-space: nowrap;
  }
  .contact-address {
    position: absolute;
    left: 0;
    right: 0;
    bottom: 46px;
    text-align: center;
    font-family: "Didact Gothic", sans-serif;
    font-size: 15px;
    letter-spacing: 0.08em;
    white-space: nowrap;
  }
</style>
</head>
<body>
  <section class="card card--brand" aria-label="Brand side">
    <svg class="brand-mark" viewBox="0 0 92 92" aria-hidden="true">
      <circle cx="46" cy="46" r="45" fill="none" stroke="#e6e6e6" stroke-width="1.2"/>
    </svg>
    <p class="brand-name">tallow hearths</p>
  </section>

  <section class="card card--contact" aria-label="Contact side">
    <h1 class="contact-name">Derek Fawcett</h1>
    <span class="contact-divider"></span>
    <ul class="contact-details">
      <li>07912488265</li>
      <li>info@tallowhearths.com</li>
      <li>www.tallowhearths.com</li>
    </ul>
    <p class="contact-address">42 mill row , ashbrook , bt19 4qa</p>
  </section>
</body>
</html>
```